Off Campus Housing website service for universities needs corporate brochure

We need a corporate brochure targeted at universities to get them to partner with us to offer an Off-Campus Housing website with housing listings and educational resources for their students. We provide hosted software and support, off-campus housing listings, and educational resources to embed in the university website (i.e http://rentalhub.wvx.edu); the university promotes the service to off-campus students, parents, and faculty/staff. We have a dedicated account executive to work with each university to promote the website to property managers in the schools area who pay to list their properties on the site. We currently partner with over 100 colleges and universities across the country to serve the needs of their off-campus students. Our corporate website is: www.lodgebridgeallies.com.
Updates

Target Market(s)

Universities and Colleges

Industry/Entity Type

Marketing

Font styles to use
Serif

Requirements
Must have
• Our logo
• Our website (www.lodgebridgeallies.com)
• Contact information (this is different than what we used on our previous brochure, image attached):
• Email: sales@lodgebridgeallies.com
• Student image(s) - must be diverse
• Phone: 877-461-7308
Nice to have
• University/Campus image (generic)

```html
<!DOCTYPE html>
<html lang="en">
<head>
<meta charset="utf-8">
<title>Lodgebridge Allies Brochure</title>
<link href="https://fonts.googleapis.com/css2?family=Libre+Baskerville:wght@400;700&family=Lora:wght@400;500;700&display=swap" rel="stylesheet">
<style>
  :root {
    --brand-blue: #1f5fbf;
    --brand-blue-deep: #174ea6;
    --ink-grey: #3f3f42;
    --paper: #ffffff;
    --backdrop: #e4e4e6;
    --tab-grey: #b9bcc2;
  }
  * { box-sizing: border-box; margin: 0; padding: 0; }
  html, body { width: 1200px; height: 1200px; overflow: hidden; }
  body { background: var(--backdrop); font-family: "Lora", serif; position: relative; }

  .spread { position: absolute; left: 110px; top: 250px; width: 980px; height: 700px; display: flex; box-shadow: 0 20px 40px rgba(0,0,0,.18); }
  .page { position: relative; width: 490px; height: 700px; overflow: hidden; }

  /* Back cover */
  .back-cover { background: var(--brand-blue); color: var(--paper); }
  .back-cover .campus-wash { position: absolute; inset: 0 0 140px 0; background: linear-gradient(180deg, rgba(255,255,255,.08), rgba(10,40,110,.18)); }
  .contact { position: absolute; top: 250px; left: 0; width: 100%; text-align: center; }
  .contact-title { font-family: "Libre Baskerville", serif; font-weight: 700; font-size: 18px; letter-spacing: .5px; }
  .contact-company { font-size: 20px; margin-top: 4px; }
  .contact-columns { display: flex; justify-content: center; gap: 34px; margin-top: 22px; text-align: left; font-size: 14px; line-height: 1.4; }
  .contact-line { display: flex; align-items: center; gap: 7px; }
  .contact-line svg { width: 11px; height: 11px; flex: none; }
  .address { display: flex; gap: 7px; }
  .address svg { width: 10px; height: 13px; margin-top: 3px; flex: none; }

  .tab-band { position: absolute; left: 20px; right: 20px; bottom: 118px; height: 24px; background: var(--tab-grey); }
  .logo-tab { position: absolute; left: 40px; right: 40px; bottom: 0; height: 130px; background: var(--paper); border-radius: 30px 30px 0 0; }
  .wordmark { display: flex; align-items: center; justify-content: center; gap: 10px; font-family: "Libre Baskerville", serif; font-weight: 700; color: var(--brand-blue); letter-spacing: 3px; }
  .wordmark .mark { width: 18px; height: 18px; background: var(--brand-blue); flex: none; }
  .logo-tab .wordmark { position: absolute; top: 36px; left: 0; right: 0; font-size: 20px; }

  /* Front cover */
  .front-cover { background: var(--paper); }
  .front-cover .wordmark { position: absolute; top: 44px; left: 0; right: 0; font-size: 21px; }
  .photo-row { position: absolute; top: 110px; left: 28px; right: 28px; height: 260px; display: flex; gap: 14px; }
  .photo { flex: 1; }
  .photo-campus { background: linear-gradient(180deg, #4f86d6 0%, #dfe4ea 45%, #c9c4bb 75%, #7f8e4a 100%); }
  .photo-student { background: linear-gradient(160deg, #e8e3d6 0%, #9fb4d9 50%, #e98a3f 100%); }
  .photo-divider { width: 4px; background: var(--brand-blue); flex: none; }
  .headline { position: absolute; top: 400px; left: 0; right: 0; text-align: center; font-weight: 400; }
  .headline-lead { font-family: "Libre Baskerville", serif; font-weight: 700; font-size: 38px; color: var(--ink-grey); letter-spacing: 1px; }
  .headline-rest { display: inline-block; margin-top: 6px; font-family: "Lora", serif; font-weight: 400; font-size: 34px; line-height: 1.15; color: var(--brand-blue); }
  .url-bar { position: absolute; top: 572px; left: 62px; right: 62px; height: 32px; background: var(--brand-blue); color: var(--paper); display: flex; align-items: center; justify-content: center; font-size: 14px; font-weight: 700; letter-spacing: 3px; }
</style>
</head>
<body>
  <main class="spread">
    <section class="page back-cover">
      <div class="campus-wash" role="img" aria-label="Faint photo of a columned campus building"></div>
      <div class="contact">
        <h2 class="contact-title">CONTACT US</h2>
        <p class="contact-company">Lodgebridge Allies, LLC</p>
        <div class="contact-columns">
          <div class="phones">
            <p class="contact-line"><svg viewBox="0 0 12 12"><path d="M2 1l2 0 1 3-1.5 1a6 6 0 0 0 3 3L8 6.5l3 1v2l-1 1.5C5 11 1 7 1 2z" fill="#fff"/></svg>877-461-7308</p>
            <p class="contact-line"><svg viewBox="0 0 12 12"><path d="M2 1l2 0 1 3-1.5 1a6 6 0 0 0 3 3L8 6.5l3 1v2l-1 1.5C5 11 1 7 1 2z" fill="#fff"/></svg>(434) 552-0187</p>
            <p class="contact-line"><svg viewBox="0 0 12 12"><path d="M2 1l2 0 1 3-1.5 1a6 6 0 0 0 3 3L8 6.5l3 1v2l-1 1.5C5 11 1 7 1 2z" fill="#fff"/></svg>(434) 608-2940</p>
          </div>
          <div class="address">
            <svg viewBox="0 0 10 13"><path d="M5 0a5 5 0 0 1 5 5c0 3-5 8-5 8S0 8 0 5a5 5 0 0 1 5-5z" fill="#fff"/><circle cx="5" cy="5" r="1.8" fill="#1f5fbf"/></svg>
            <p>PO Box 3817,<br>Brookhaven, VA 22941-3817<br>sales@lodgebridgeallies.com</p>
          </div>
        </div>
      </div>
      <div class="tab-band"></div>
      <div class="logo-tab">
        <div class="wordmark"><span class="mark"></span><span>LODGEBRIDGE ALLIES</span></div>
      </div>
    </section>

    <section class="page front-cover">
      <div class="wordmark"><span class="mark"></span><span>LODGEBRIDGE ALLIES</span></div>
      <div class="photo-row">
        <div class="photo photo-campus" role="img" aria-label="Photo of a white columned university building on a lawn"></div>
        <div class="photo-divider"></div>
        <div class="photo photo-student" role="img" aria-label="Photo of a student working on a laptop on an orange sofa"></div>
      </div>
      <h1 class="headline">
        <span class="headline-lead">SIMPLIFYING</span><br>
        <span class="headline-rest">THE OFF-CAMPUS<br>HOUSING EXPERIENCE</span>
      </h1>
      <p class="url-bar">www.lodgebridgeallies.com</p>
    </section>
  </main>
</body>
</html>
```